Health Supplement Series for 60 tablets of pure Amber Vine Core powder

We need a packaging design theme for a health supplement for international consumers. Our initial product is called 'Amber Vine Core'. It is for general health and is particularly effective for diabetic symptoms.
We would like to see designs that are clean and fresh.
It should give the impression of professional, premium pharmaceutical grade products.
Our company logo is attached below.

Target Market(s)

International

Industry/Entity Type

Health And Wellness

Font styles to use
Serif
Sans Serif

Requirements
Must have
• Bottle and box packaging required.
• 1st product is bottle of 60 tablets of 0.5gm each.
Should not have
• Seals and other "must buy" "guaranteed" etc

```html
<!DOCTYPE html>
<html lang="en">
<head>
<meta charset="utf-8">
<title>Amber Vine Core – Bottle Label</title>
<link rel="stylesheet" href="https://fonts.googleapis.com/css2?family=Kanit:wght@500;700&family=Roboto:wght@400&display=swap">
<style>
  :root {
    --bg: #efefef;
    --label: #ffffff;
    --orange: #e8602a;
    --orange-deep: #d9501c;
    --brand-green: #6ea83a;
    --body-text: #6b6b6b;
    --seed-light: #b06a3a;
    --seed-dark: #4a2a1c;
  }
  html, body {
    margin: 0;
    padding: 0;
    width: 1158px;
    height: 1200px;
    overflow: hidden;
    background: var(--bg);
  }
  .canvas {
    position: relative;
    width: 1158px;
    height: 1200px;
  }
  .label {
    position: absolute;
    left: 149px;
    top: 30px;
    width: 860px;
    height: 1140px;
    display: block;
    filter: drop-shadow(0 6px 18px rgba(0,0,0,0.12));
  }
  .label-base { fill: var(--label); }
  .band { fill: var(--orange); }
  .band-edge { fill: var(--orange-deep); }
  .frame { fill: none; stroke: var(--orange); stroke-width: 2.2; }
  .brand-mark { fill: var(--brand-green); }
  .brand-name {
    font-family: "Kanit", sans-serif;
    font-weight: 500;
    font-size: 15px;
    letter-spacing: 1px;
    fill: var(--brand-green);
  }
  .product-name {
    font-family: "Kanit", sans-serif;
    font-weight: 700;
    font-size: 61px;
    letter-spacing: -1.5px;
    fill: var(--orange);
  }
  .side-copy {
    font-family: "Roboto", sans-serif;
    font-weight: 400;
    font-size: 8.6px;
    fill: var(--body-text);
  }
</style>
</head>
<body>
<main class="canvas">
  <svg class="label" viewBox="0 0 400 530" xmlns="http://www.w3.org/2000/svg">
    <defs>
      <linearGradient id="seedTone" x1="0" y1="0" x2="1" y2="0">
        <stop offset="0" stop-color="var(--seed-light)"/>
        <stop offset="1" stop-color="var(--seed-dark)"/>
      </linearGradient>
    </defs>

    <rect class="label-base" x="0" y="0" width="400" height="530"/>

    <!-- top band -->
    <path class="band" d="M0,0 H400 V18 Q220,10 0,14 Z"/>
    <path class="band-edge" d="M0,14 Q220,10 400,18 V21 Q220,13 0,17 Z"/>

    <!-- bottom band -->
    <path class="band" d="M0,516 Q200,506 400,506 V530 H0 Z"/>
    <path class="band-edge" d="M0,512 Q200,502 400,503 V506 Q200,506 0,516 Z"/>

    <!-- leaf frame -->
    <path class="frame" d="M323,45 L323,440 Q323,470 290,472 L92,480 Q55,482 55,445 L55,275 Q55,225 110,205 Q200,182 270,162 Q318,142 323,45 Z"/>

    <!-- brand -->
    <rect class="brand-mark" x="85" y="115" width="16" height="22"/>
    <text class="brand-name" x="106" y="132">NERIDA BIOTECH</text>

    <!-- product name -->
    <text class="product-name" text-anchor="middle" x="196" y="255">AMBER</text>
    <text class="product-name" text-anchor="middle" x="196" y="307">VINE</text>
    <text class="product-name" text-anchor="middle" x="196" y="359">CORE</text>

    <!-- ingredient image area -->
    <ellipse role="img" aria-label="Photo of whole and halved dried fruit seeds" cx="198" cy="420" rx="72" ry="30" fill="url(#seedTone)"/>

    <!-- side copy -->
    <text class="side-copy" transform="translate(352,435) rotate(-90)">Lorem ipsum dolor sit amet, consectetur adipisc-</text>
    <text class="side-copy" transform="translate(364,435) rotate(-90)">ing elit. Ut mollis lobortis tempus. Donec lobortis</text>
  </svg>
</main>
</body>
</html>
```